Chartered Professional Accounting Firm Needs a Business Card Design

We need a card design for an accounting firm based in Toronto, Ontario. The firm name is Pavel Ostrom Professional Corporation. The owner of the firm is a chartered professional accountant and a certified general accountant. Services of the firm include 60% tax preparation and consulting and 40% financial statements for corporation year-end. We would like a modern design. The color could be black, white, gray, blue or other color to bring more confidence to clients. The logo of the firm should be included in the design. Thanks

Name: Pavel Ostrom, CPA, CGA Address: 47 Maple Crest Rd. Richmond Hill, ON L7K 3B5 Telephone: (416) 562-3907 Fax:(416) 734-2165 Email: pavel@pavelostrom-example.ca

Accounting

```html
<!DOCTYPE html>
<html lang="en">
<head>
<meta charset="utf-8">
<title>Pavel Ostrom Professional Corporation – Business Card</title>
<link rel="stylesheet" href="https://fonts.googleapis.com/css2?family=Cinzel:wght@700&family=Marcellus&family=Jost:wght@400;500&display=swap">
<style>
  :root {
    --backdrop: #d9d6d0;
    --card: #ececec;
    --brand-blue: #2e35a0;
    --grey-text: #8a8a8a;
    --shadow: rgba(0, 0, 0, 0.18);
  }
  * { box-sizing: border-box; margin: 0; padding: 0; }
  html, body {
    width: 1200px;
    height: 800px;
    overflow: hidden;
    background: var(--backdrop);
  }
  .canvas {
    position: relative;
    width: 1200px;
    height: 800px;
    display: flex;
    align-items: center;
    justify-content: center;
    gap: 50px;
  }
  .card {
    position: relative;
    width: 540px;
    height: 310px;
    background: var(--card);
    box-shadow: 0 10px 24px var(--shadow);
    overflow: hidden;
  }
  .card__tab {
    position: absolute;
    width: 190px;
    height: 12px;
    background: var(--brand-blue);
    border-radius: 6px;
  }
  .card__tab--top { top: -6px; right: 30px; }
  .card__tab--bottom { bottom: -6px; left: 30px; }

  .brand {
    display: flex;
    align-items: center;
    gap: 12px;
  }
  .brand__mark {
    width: 40px;
    height: 40px;
    background: var(--brand-blue);
    flex: none;
  }
  .brand__name {
    font-family: "Cinzel", serif;
    font-weight: 700;
    color: var(--brand-blue);
    line-height: 1.05;
  }
  .brand__name .line-main { display: block; font-size: 26px; letter-spacing: 0.5px; }
  .brand__name .line-sub { display: block; font-size: 10.5px; letter-spacing: 0.4px; }
  .brand__credentials {
    font-family: "Marcellus", serif;
    font-size: 8.5px;
    letter-spacing: 0.6px;
    color: var(--grey-text);
    text-transform: uppercase;
    line-height: 1.25;
    margin-top: 2px;
  }

  .card--front .brand-block {
    position: absolute;
    left: 50%;
    top: 50%;
    transform: translate(-50%, -50%);
  }
  .card--front .brand__credentials { padding-left: 52px; }

  .card--back .brand-block {
    position: absolute;
    left: 70px;
    top: 42px;
  }
  .card--back .brand__credentials { padding-left: 52px; }

  .contact {
    position: absolute;
    left: 175px;
    top: 140px;
    color: var(--brand-blue);
    font-family: "Jost", sans-serif;
  }
  .contact__name {
    font-family: "Marcellus", serif;
    font-size: 20px;
    letter-spacing: 1.5px;
    text-transform: uppercase;
    line-height: 1.1;
  }
  .contact__title {
    font-size: 13px;
    font-weight: 500;
    margin: 2px 0 0 40px;
  }
  .contact__list {
    list-style: none;
    margin: 18px 0 0 70px;
    font-size: 13px;
    font-weight: 500;
    line-height: 1.55;
  }
  .contact__address {
    margin-top: 14px;
    font-size: 13px;
    font-weight: 500;
  }
</style>
</head>
<body>
<main class="canvas">

  <section class="card card--front" aria-label="Card front">
    <span class="card__tab card__tab--top"></span>
    <span class="card__tab card__tab--bottom"></span>
    <div class="brand-block">
      <div class="brand">
        <span class="brand__mark"></span>
        <span class="brand__name">
          <span class="line-main">PAVEL OSTROM</span>
          <span class="line-sub">PROFESSIONAL CORPORATION</span>
        </span>
      </div>
      <p class="brand__credentials">Chartered Professional Accountant<br>Certified General Accountant</p>
    </div>
  </section>

  <section class="card card--back" aria-label="Card back">
    <span class="card__tab card__tab--top"></span>
    <span class="card__tab card__tab--bottom"></span>
    <div class="brand-block">
      <div class="brand">
        <span class="brand__mark"></span>
        <span class="brand__name">
          <span class="line-main">PAVEL OSTROM</span>
          <span class="line-sub">PROFESSIONAL CORPORATION</span>
        </span>
      </div>
      <p class="brand__credentials">Chartered Professional Accountant<br>Certified General Accountant</p>
    </div>
    <div class="contact">
      <p class="contact__name">Pavel Ostrom</p>
      <p class="contact__title">CPA, CGA</p>
      <ul class="contact__list">
        <li>(416) 562-3907</li>
        <li>(416) 734-2165</li>
        <li>pavel@pavelostrom-example.ca</li>
      </ul>
      <p class="contact__address">47 Maple Crest Rd. Richmond Hill, ON L7K 3B5</p>
    </div>
  </section>

</main>
</body>
</html>
```